Brochure and Business Card design

I am looking for a high end, elegant A4, 4 page brochure booklet to convey our products to clientele that will be visiting a luxury display showroom.

Harrowgate Locks and Grilles is a Australian security provider, and we supply high end products from reputable brands.
The brochure will be directed to clients building a new home with a partnered building company and will be accompanied with display boards of our products.

I am providing files of a document we have put together with the relevant information and some images to help along the way, we are not bound by the layout or style it has been drawn up and we wish to give you complete creative freedom putting the peaces together. I have also provided the files for our logo in two different colours, and a picture of a brochure we love the look of.

If you have any suggestions, we can likely come up with further images etc if it will help or even if you feel some should be removed, we are open to that also

Target Market(s)

Young familys, people building new luxury homes, proffesionals, home owners

Industry/Entity Type

Business

Font styles to use
Serif
Sans Serif

Requirements
Must have
• All 8 pages
Should not have
• Not really a fan of reds and similar.

```html
<!DOCTYPE html>
<html lang="en">
<head>
<meta charset="utf-8">
<title>Harrowgate Locks and Grilles – Showroom Brochure Spreads</title>
<link rel="stylesheet" href="https://fonts.googleapis.com/css2?family=Didact+Gothic&family=Open+Sans:wght@400;600;700&display=swap">
<style>
  :root{
    --backdrop:#c4c4c4;
    --backdrop-light:#dcdcdc;
    --paper:#ffffff;
    --paper-shade:#f1f1f1;
    --brand-blue:#2a86c6;
    --brand-blue-dark:#1f6ea8;
    --brand-green:#86bd3e;
    --ink:#4a4a4a;
    --ink-soft:#9a9a9a;
    --title-blue:#3a9ad6;
    --photo-grey:#b7b3ad;
    --photo-warm:#cdb8a0;
    --photo-sky:#c9d9e6;
  }
  *{box-sizing:border-box;margin:0;padding:0}
  html,body{width:1200px;height:754px;overflow:hidden}
  body{font-family:"Open Sans",Arial,sans-serif;color:var(--ink)}
  .canvas{position:relative;width:1200px;height:754px;
    background:radial-gradient(ellipse at 50% 35%,var(--backdrop-light),var(--backdrop));}
  .spread{position:absolute;width:540px;height:300px;display:flex;
    box-shadow:0 10px 22px rgba(0,0,0,.22)}
  .spread--cover{left:30px;top:38px}
  .spread--alarm{left:630px;top:38px}
  .spread--mesh{left:30px;top:416px}
  .spread--vacuum{left:630px;top:416px}
  .page{position:relative;width:270px;height:300px;background:var(--paper);overflow:hidden}
  .page--left{background:linear-gradient(90deg,var(--paper) 88%,var(--paper-shade))}
  .page--right{background:linear-gradient(90deg,var(--paper-shade),var(--paper) 12%)}
  .abs{position:absolute}
  .photo{position:absolute;background:linear-gradient(135deg,var(--photo-sky),var(--photo-grey))}
  .photo--warm{background:linear-gradient(135deg,var(--photo-warm),var(--photo-grey))}
  .photo--dark{background:linear-gradient(135deg,#8c8c8c,#3f3f3f)}
  .block{position:absolute}
  .block--green{background:var(--brand-green)}
  .block--blue{background:var(--brand-blue)}
  .brand-name{font-family:"Didact Gothic",sans-serif;color:var(--ink);letter-spacing:.06em;display:flex;align-items:center;gap:5px}
  .brand-dot{width:9px;height:9px;border-radius:50%;background:var(--brand-green)}
  .small{font-size:5px;line-height:1.55;color:var(--ink-soft)}
  .heading{font-family:"Didact Gothic",sans-serif;color:var(--title-blue);font-size:15px}
  .subhead{font-family:"Open Sans",sans-serif;font-weight:700;color:var(--brand-green);font-size:5.5px;margin-bottom:2px}
  .subhead--blue{color:var(--title-blue)}
  .thumb{position:absolute;background:linear-gradient(135deg,#e7e7e7,#bdbdbd)}
  .label{font-size:4.5px;line-height:1.4;color:var(--ink-soft)}
  .on-color{color:#fff}
  .services{font-family:"Didact Gothic",sans-serif;font-size:6.5px;line-height:1.6;color:#c2c2c2;text-align:right}
</style>
</head>
<body>
<main class="canvas">

  <!-- Back and front cover -->
  <section class="spread spread--cover">
    <div class="page page--left">
      <div class="brand-name abs" style="left:88px;top:62px;font-size:12px"><span class="brand-dot"></span>HARROWGATE</div>
      <p class="small abs" style="left:38px;top:90px;width:194px;text-align:center">Harrowgate Locks and Grilles is a trusted supplier of quality home security products, working with leading builders to deliver secure, stylish homes.</p>
      <p class="small abs" style="left:38px;top:116px;width:194px;text-align:center">Visit our showroom to see the full range on display.</p>
      <div class="block block--blue" style="left:0;top:150px;width:270px;height:150px;background:linear-gradient(120deg,var(--brand-blue-dark),var(--brand-blue) 60%,#5aa9dc)"></div>
      <p class="abs on-color" style="left:0;top:178px;width:270px;text-align:center;font-size:6px;font-weight:700">For all inquiries</p>
      <p class="abs on-color" style="left:0;top:190px;width:270px;text-align:center;font-size:4.8px">Email: info@harrowgatelocks.com.au &nbsp;|&nbsp; Phone: 1300 000 000</p>
      <p class="abs on-color" style="left:0;top:202px;width:270px;text-align:center;font-size:7px;font-weight:700">www.harrowgatelocks.com.au</p>
      <p class="abs on-color" style="left:0;top:250px;width:270px;text-align:center;font-size:4.5px;opacity:.7">Servicing all of Sydney and surrounding suburbs</p>
    </div>
    <div class="page page--right">
      <div class="photo" style="left:18px;top:22px;width:56px;height:56px" role="img" aria-label="Photo of a modern home facade with security screens"></div>
      <div class="block block--green" style="left:76px;top:22px;width:56px;height:56px"></div>
      <div class="photo photo--warm" style="left:134px;top:22px;width:56px;height:56px" role="img" aria-label="Photo of a new townhouse exterior"></div>
      <div class="block block--blue" style="left:18px;top:80px;width:56px;height:56px"></div>
      <div class="photo photo--warm" style="left:76px;top:80px;width:56px;height:56px" role="img" aria-label="Photo of a two storey home front"></div>
      <div class="photo photo--dark" style="left:18px;top:138px;width:56px;height:56px" role="img" aria-label="Photo of a wall mounted intercom panel"></div>
      <div class="services abs" style="right:22px;top:110px">Alarm Systems<br>Intercom<br>Stalwart Mesh<br>Ducted Vacuum</div>
      <div class="brand-name abs" style="right:22px;top:212px;font-size:12px"><span class="brand-dot"></span>HARROWGATE</div>
      <p class="abs" style="right:22px;top:230px;font-size:5px;color:var(--ink-soft)">www.harrowgatelocks.com.au</p>
    </div>
  </section>

  <!-- Alarm systems and intercom -->
  <section class="spread spread--alarm">
    <div class="page page--left">
      <h2 class="heading abs" style="left:18px;top:16px">Alarm Systems</h2>
      <p class="small abs" style="left:18px;top:40px;width:110px">A monitored alarm keeps your family safe day and night. Our systems are simple to use, quick to arm and can be controlled from your phone wherever you are in the world.</p>
      <div class="photo" style="left:140px;top:14px;width:112px;height:56px" role="img" aria-label="Photo of an alarm keypad on a wall"></div>
      <p class="subhead abs" style="left:140px;top:76px">Home Kit</p>
      <div class="block block--blue abs" style="left:130px;top:90px;width:140px;height:18px"></div>
      <p class="abs on-color" style="left:136px;top:95px;font-size:5px">Ask about our smart app control for your alarm</p>
      <p class="subhead abs" style="left:18px;top:118px">Popular Upgrades</p>
      <div class="thumb" style="left:18px;top:134px;width:22px;height:22px" role="img" aria-label="Product shot of an alarm keypad"></div>
      <p class="label abs" style="left:44px;top:140px">Touch Keypad</p>
      <div class="thumb" style="left:90px;top:134px;width:22px;height:22px" role="img" aria-label="Product shot of a remote fob"></div>
      <p class="label abs" style="left:116px;top:140px">Remote Fob</p>
      <div class="thumb" style="left:160px;top:134px;width:22px;height:22px" role="img" aria-label="Product shot of a ceiling sensor"></div>
      <p class="label abs" style="left:186px;top:140px">Ceiling Sensor</p>
      <div class="thumb" style="left:50px;top:166px;width:22px;height:22px" role="img" aria-label="Product shot of a motion detector"></div>
      <p class="label abs" style="left:76px;top:172px">Motion Detector</p>
      <div class="thumb" style="left:130px;top:166px;width:22px;height:22px" role="img" aria-label="Product shot of a smoke detector"></div>
      <p class="label abs" style="left:156px;top:172px">Smoke Detector</p>
    </div>
    <div class="page page--right">
      <h2 class="heading abs" style="left:18px;top:16px">Intercom</h2>
      <p class="small abs" style="left:18px;top:38px;width:120px">See and speak with visitors before opening the door. Our video intercoms bring clear picture and sound to every entry of your new home.</p>
      <div class="photo photo--warm" style="left:150px;top:14px;width:106px;height:56px" role="img" aria-label="Photo of a bright hallway with an indoor intercom screen"></div>
      <p class="subhead abs" style="left:180px;top:78px">Popular Upgrades</p>
      <div class="thumb" style="left:18px;top:86px;width:18px;height:18px" role="img" aria-label="Product shot of a seven inch video monitor"></div>
      <div class="abs" style="left:42px;top:84px;width:120px"><p class="subhead subhead--blue">7" Colour Video Intercom</p><p class="small">Large touch screen with memory and hands free talk.</p></div>
      <div class="thumb" style="left:18px;top:120px;width:18px;height:18px" role="img" aria-label="Product shot of a compact video monitor"></div>
      <div class="abs" style="left:42px;top:118px;width:120px"><p class="subhead subhead--blue">4.3" Colour Video Intercom</p><p class="small">Compact monitor with clear picture and door release.</p></div>
      <div class="thumb" style="left:18px;top:154px;width:18px;height:18px" role="img" aria-label="Product shot of an audio handset"></div>
      <div class="abs" style="left:42px;top:152px;width:120px"><p class="subhead subhead--blue">Audio Only Intercom</p><p class="small">Simple handset for clear voice calls at the gate.</p></div>
      <div class="thumb" style="left:180px;top:94px;width:18px;height:18px" role="img" aria-label="Product shot of a door station"></div>
      <p class="label abs" style="left:202px;top:98px">Extra door station</p>
      <div class="thumb" style="left:180px;top:124px;width:18px;height:18px" role="img" aria-label="Product shot of a gate release"></div>
      <p class="label abs" style="left:202px;top:128px">Electric gate release</p>
      <div class="thumb" style="left:180px;top:154px;width:18px;height:18px" role="img" aria-label="Product shot of a second monitor"></div>
      <p class="label abs" style="left:202px;top:158px">Second indoor monitor</p>
    </div>
  </section>

  <!-- Security mesh -->
  <section class="spread spread--mesh">
    <div class="page page--left">
      <div class="photo photo--dark" style="left:0;top:0;width:270px;height:150px" role="img" aria-label="Close-up photo of a security mesh door and handle"></div>
      <svg class="abs" style="left:0;top:0" width="270" height="300" viewBox="0 0 270 300" aria-hidden="true">
        <defs><linearGradient id="meshBand" x1="0" y1="0" x2="1" y2="1"><stop offset="0" stop-color="#1f6ea8"/><stop offset=".6" stop-color="#2a86c6"/><stop offset="1" stop-color="#5aa9dc"/></linearGradient></defs>
        <path d="M0 118 C90 92 190 98 270 128 L270 300 L0 300 Z" fill="url(#meshBand)"/>
      </svg>
      <h2 class="heading abs on-color" style="left:60px;top:150px;font-size:14px;color:#fff">Why Stalwart Mesh?</h2>
      <p class="small abs on-color" style="left:60px;top:174px;width:170px;color:#e4f0f9">Stalwart Mesh screens combine strength and style, keeping intruders out while letting fresh air and light in. Built tough for Australian homes and made to last.</p>
    </div>
    <div class="page page--right">
      <div class="thumb" style="left:18px;top:30px;width:38px;height:26px" role="img" aria-label="Diagram of mesh strength test"></div>
      <div class="abs" style="left:66px;top:28px;width:180px"><p class="subhead">Toughness</p><p class="small">Stainless steel mesh resists knife, impact and pry attacks with ease.</p></div>
      <div class="thumb" style="left:18px;top:80px;width:38px;height:26px" role="img" aria-label="Diagram of mesh visibility"></div>
      <div class="abs" style="left:66px;top:78px;width:180px"><p class="subhead">Visibility</p><p class="small">Fine weave keeps a clear view outside while giving daytime privacy.</p></div>
      <div class="thumb" style="left:18px;top:130px;width:38px;height:26px" role="img" aria-label="Diagram of airflow through mesh"></div>
      <div class="abs" style="left:66px;top:128px;width:180px"><p class="subhead">Airflow Ratio</p><p class="small">Open mesh lets breezes flow through to keep your home cool.</p></div>
      <div class="thumb" style="left:18px;top:180px;width:38px;height:26px" role="img" aria-label="Diagram of frame profile"></div>
      <div class="abs" style="left:66px;top:178px;width:180px"><p class="subhead">Premium Design</p><p class="small">Slim frames in a range of colours suit any modern home design.</p></div>
    </div>
  </section>

  <!-- Ducted vacuum -->
  <section class="spread spread--vacuum">
    <div class="page page--left">
      <div class="photo photo--warm" style="left:0;top:0;width:270px;height:150px" role="img" aria-label="Photo of a smiling family relaxing at home"></div>
      <svg class="abs" style="left:0;top:0" width="270" height="300" viewBox="0 0 270 300" aria-hidden="true">
        <path d="M0 112 C90 88 190 96 270 126 L270 300 L0 300 Z" fill="#86bd3e"/>
      </svg>
      <div class="thumb" style="left:14px;top:126px;width:70px;height:50px;background:linear-gradient(135deg,#6f6f6f,#2f2f2f)" role="img" aria-label="Product shot of vacuum hose and cleaning tools"></div>
      <h2 class="heading abs" style="left:104px;top:140px;font-size:14px;color:#fff">Ducted Vacuum</h2>
      <p class="small abs" style="left:104px;top:164px;width:140px;color:#eef6e3">A ducted vacuum removes dust from every room quietly, with no heavy machine to carry up the stairs.</p>
    </div>
    <div class="page page--right">
      <div class="thumb" style="left:18px;top:40px;width:64px;height:110px;border-radius:8px;background:linear-gradient(90deg,#6b7078,#9aa0a8 50%,#5b6068)" role="img" aria-label="Product shot of a ducted vacuum power unit"></div>
      <div class="abs" style="left:98px;top:40px;width:70px"><p class="subhead">No Dust Back Into Your Home</p><p class="small">Dust is carried away to the garage unit, so air stays clean.</p></div>
      <div class="abs" style="left:178px;top:40px;width:76px"><p class="subhead">Whole House Reach</p><p class="small">Inlets in each room give fast, easy cleaning throughout.</p></div>
      <div class="abs" style="left:98px;top:110px;width:70px"><p class="subhead">Quiet Power Cleaning</p><p class="small">The motor sits outside, so cleaning is calm and quiet inside.</p></div>
      <div class="abs" style="left:178px;top:110px;width:76px"><p class="subhead">Full Tool Set Included</p><p class="small">Hose, wands and heads come ready for floors and rugs.</p></div>
    </div>
  </section>

</main>
</body>
</html>
```